Young Architect Bussiness Card

English is not my first language (spanish is).
Need a bussiness card design for my best friend who is about to graduate from college, Licentiate degree in architecture, so she needs business cards to start networking, currently she has no porfolio, web page or plazared. so she is relying on her cel phone and correovela, but should leave space for one of them (plazared)

Design for business card should be modern, maybe something with construction blue prints patern or 3D modelling.

Name: Mariela Otárola Bonilla
Licentiate in Arquitecture
Cel: (506) XXX-4827
email: marielaXXX@correovela.com

Services, although im not sure if it has to be there or not:
Anteproyectos / Proposal design
Inspecciones / Site Inspections
Modelado 3D / 3D modelling
Planos Constructivos / Construction Blue Prints
Presupuestos / Budgets

Design should be in spanish

Industry/Entity Type

Architect

Contact Information for Business Card

Name: Mariela Otárola, Arquitecto
Associtation code : XXXX
Phone: (506) XXXX-XXXX
Email: xxx@correovela.com
Plazared: xxxx

Requirements
Must have
• Design for business card should be modern, maybe something with construction blue prints patern or 3D modelling.
Nice to have
• Something like a transition from 2D to 3D.

```html
<!DOCTYPE html>
<html lang="es">
<head>
<meta charset="UTF-8">
<title>Tarjeta de presentación — Mariela Otárola Bonilla</title>
<link rel="stylesheet" href="https://fonts.googleapis.com/css2?family=Lato:wght@400;700&display=swap">
<style>
  :root {
    --bg: #2a2a2a;
    --paper: #ffffff;
    --ink: #1f1f1f;
    --night: #000000;
    --gold: #f2c200;
    --gold-light: #fbe24a;
    --gold-deep: #b88a00;
    --white-text: #f4f4f4;
  }
  * { box-sizing: border-box; margin: 0; padding: 0; }
  html, body {
    width: 1200px; height: 880px; overflow: hidden;
    background: var(--bg);
    font-family: "Lato", sans-serif;
  }
  .canvas { position: relative; width: 1200px; height: 880px; }
  .card {
    position: absolute;
    width: 640px; height: 366px;
    border-radius: 20px;
    overflow: hidden;
    box-shadow: 0 10px 28px rgba(0,0,0,0.45);
  }
  .card--front { left: 120px; top: 56px; background: var(--paper); }
  .card--back { left: 440px; top: 458px; background: var(--night); }

  .cubes-art {
    position: absolute;
    top: 0; right: 0;
    border-radius: 0 20px 40px 110px;
    background: radial-gradient(ellipse at 60% 40%, var(--gold-light) 0%, var(--gold) 45%, var(--gold-deep) 80%, rgba(184,138,0,0) 100%);
  }
  .card--front .cubes-art { width: 250px; height: 290px; }
  .card--back .cubes-art { width: 310px; height: 200px; }

  .accent-dot {
    position: absolute;
    left: -20px; top: 170px;
    width: 40px; height: 40px;
    border-radius: 50%;
    background: var(--gold);
  }
  .identity { position: absolute; left: 44px; top: 156px; }
  .identity__name {
    color: var(--gold);
    font-size: 22px; font-weight: 400;
    letter-spacing: 0.4px;
    text-transform: uppercase;
    white-space: nowrap;
  }
  .identity__title { color: var(--ink); font-size: 17px; margin-top: 2px; }
  .contact {
    position: absolute; left: 44px; bottom: 36px;
    font-size: 19px; line-height: 1.3;
    color: var(--ink);
  }
  .contact__label { color: var(--gold); }

  .services {
    position: absolute; left: 40px; bottom: 36px;
    color: var(--white-text);
  }
  .services__heading {
    color: var(--gold);
    font-size: 20px; font-weight: 700;
    margin-bottom: 12px;
  }
  .services__list { list-style: none; font-size: 18px; line-height: 1.28; white-space: nowrap; }
</style>
</head>
<body>
<main class="canvas">
  <section class="card card--front">
    <div class="cubes-art" role="img" aria-label="Ilustración de cubos amarillos flotando en 3D"></div>
    <span class="accent-dot"></span>
    <div class="identity">
      <h1 class="identity__name">Mariela Otárola Bonilla</h1>
      <p class="identity__title">Licentiate in Arquitecture</p>
    </div>
    <div class="contact">
      <p><span class="contact__label">Cell:</span> (506) XXX-4827</p>
      <p><span class="contact__label">Email:</span> marielaXXX@correovela.com</p>
    </div>
  </section>

  <section class="card card--back">
    <div class="cubes-art" role="img" aria-label="Ilustración de cubos amarillos flotando en 3D sobre fondo negro"></div>
    <div class="services">
      <h2 class="services__heading">SERVICES</h2>
      <ul class="services__list">
        <li>Anteproyectos / Proposal design</li>
        <li>Inspecciones / Site Inspections</li>
        <li>Modelado 3D / 3D modelling</li>
        <li>Planos Constructivos / Construction Blue Prints</li>
        <li>Presupuestos / Budgets</li>
      </ul>
    </div>
  </section>
</main>
</body>
</html>
```